Business card design needed

I would like a one sided black business card with the information provided above. Refer to my website www.brightvolleyracquets.com.au for an example of colors I have used for my site, would like to keep this consistent for my business cards also, I will upload my logo below.

I am a new small business that provides tennis customers with racquet re stringing, tennis strings and accessories.

Industry/Entity Type

Small Business

Contact Information for Business Card

Bright Volley Tennis

Owen Whitby
Managing Director

brightvolleyracquets@mailbox.example
www.brightvolleyracquets.com.au
0491 726 305

Racquet Restringing/Tennis Strings/Accessories

Requirements
Must have
• Must have my logo and card must be black

```html
<!DOCTYPE html>
<html lang="en">
<head>
<meta charset="utf-8">
<title>Bright Volley Tennis – Business Card</title>
<link rel="stylesheet" href="https://fonts.googleapis.com/css2?family=Source+Sans+3:wght@400;600&display=swap">
<style>
  :root {
    --backdrop: #7a4e31;
    --card: #000000;
    --lime: #c3d52e;
    --white: #f4f4f4;
    --divider: #5a5a5a;
  }
  * { margin: 0; padding: 0; box-sizing: border-box; }
  html, body {
    width: 1200px; height: 475px; overflow: hidden;
    background: var(--backdrop);
    font-family: "Source Sans 3", "Myriad Pro", Arial, sans-serif;
  }
  .card {
    position: absolute;
    width: 546px; height: 311px;
    background: var(--card);
    border-radius: 14px;
    overflow: hidden;
  }
  .card--front { left: 31px; top: 81px; }
  .card--back  { left: 606px; top: 85px; }

  .brand {
    position: absolute;
    display: flex; align-items: center;
    color: var(--lime);
    font-weight: 600;
    white-space: nowrap;
  }
  .brand__dot { border-radius: 50%; background: var(--lime); flex: none; }
  .card--front .brand { left: 20px; top: 143px; font-size: 20px; gap: 9px; }
  .card--front .brand__dot { width: 22px; height: 22px; }
  .card--back .brand {
    left: 0; right: 0; top: 128px; justify-content: center;
    font-size: 34px; gap: 14px;
  }
  .card--back .brand__dot { width: 36px; height: 36px; }

  .divider {
    position: absolute; left: 268px; top: 86px;
    width: 1px; height: 140px; background: var(--divider);
  }
  .person { position: absolute; left: 282px; top: 90px; }
  .person__name { color: var(--lime); font-size: 20px; font-weight: 400; letter-spacing: 0.2px; line-height: 1.1; }
  .person__role { color: var(--lime); font-size: 13px; margin-top: 2px; }

  .contacts { position: absolute; left: 282px; top: 156px; list-style: none; }
  .contacts li {
    display: flex; align-items: center; gap: 9px;
    color: var(--white); font-size: 13.5px; height: 20px;
    white-space: nowrap;
  }
  .contacts svg { width: 12px; height: 12px; flex: none; }

  .web-line {
    position: absolute; left: 0; right: 0; top: 240px;
    text-align: center; color: var(--white);
    font-size: 13.5px; letter-spacing: 2px;
  }
</style>
</head>
<body>
  <section class="card card--front">
    <div class="brand"><span class="brand__dot"></span>Bright Volley Tennis</div>
    <div class="divider"></div>
    <div class="person">
      <h1 class="person__name">OWEN WHITBY</h1>
      <p class="person__role">Managing Director</p>
    </div>
    <ul class="contacts">
      <li>
        <svg viewBox="0 0 24 24" aria-hidden="true"><path fill="#c3d52e" d="M6.6 2.5l3 4-2 2.3c1.3 2.8 3.4 4.9 6.1 6.2l2.3-2 4 3-1.6 3.3c-.4.6-1.1.9-1.8.7C9.4 18.4 5.6 14.6 3.9 7.4c-.2-.7.1-1.4.7-1.8z"/></svg>
        0491 726 305
      </li>
      <li>
        <svg viewBox="0 0 24 24" aria-hidden="true"><rect x="2" y="5" width="20" height="14" rx="1.5" fill="#c3d52e"/><path d="M2.5 6l9.5 7 9.5-7" fill="none" stroke="#000" stroke-width="2"/></svg>
        brightvolleyracquets@mailbox.example
      </li>
      <li>
        <svg viewBox="0 0 24 24" aria-hidden="true" fill="none" stroke="#c3d52e" stroke-width="2"><circle cx="12" cy="12" r="10"/><ellipse cx="12" cy="12" rx="4.5" ry="10"/><path d="M2 12h20M4 7h16M4 17h16"/></svg>
        www.brightvolleyracquets.com.au
      </li>
    </ul>
  </section>

  <section class="card card--back">
    <div class="brand"><span class="brand__dot"></span>Bright Volley Tennis</div>
    <p class="web-line">www.brightvolleyracquets.com.au</p>
  </section>
</body>
</html>
```